Cards & Invitations

Hi!
We would like you to design 3 amazing cards for us.
1. Wedding invitation.
We would like to have a spring wedding invitation. It has to be A4 folded to A5 format, floral theme, but made in a very classic style. It has to contain light green and blue colors, but you are free to use other colors as well.
Text to be included:
Mr. and Mrs. Dwight Velmoran
Request the honour of your presence
At the marriage of their daughter
Maris Velmoran
to
Lionel Brask
Saturday, the eighteenth of April
Two thousand and twelve
At three o'clock in the afternoon
Saint Odric's Church
58 Wendle Street,
South Hampton, New York
Followed by a dinner at
Restaurant Ovilo, Marsh Lane 347
R.S.V.P. by the ninth of April
2. Christening invitation in Vintage style.
We need an invitation for a christening of Noel Ferrandi. We would like it to be in vintage style, in light pink or lilac color and containing the photo of the baby.
It should also have some church symbols, like cross, prayer beads etc (one element is enough, not all together). Format: A5 horisontal (landscape) card. Please, find the photo attached.
Text to be included:
You are invited to
Witness and Celebrate
the Baptism of our daughter
Noel Ferrandi
Sunday, September 26th at 1 p.m.
St. Ambers Church
5816 Tillman Row, Parktown
Reception following the ceremony
at the Ferrandi home
7392 Quillon, Pearl Sound
Please reply by September 18th
3. Birthday invitation.
This is an invitation for Noel's 7th birthday party. The theme is racing. It should contain his photo and a race car (cars) or racing competition. No color preferences. It's a square folded card. Please, find attached the photo.
Text on the outside: Noel is turning 7
Text on the inside:
You are invited to join us
for Noel's 7th Birthday Celebration
Saturday, September 18th
We will have the celebration at Tin Kettle,
947 Brindle Road, Tillman Row
Please reply by September 7th
to Rud at 587-649-302
Welcome!

```html
<!DOCTYPE html>
<html lang="en">
<head>
<meta charset="utf-8">
<title>Wedding Invitation – Velmoran &amp; Brask</title>
<link rel="stylesheet" href="https://fonts.googleapis.com/css2?family=Great+Vibes&family=Pinyon+Script&family=Questrial&display=swap">
<style>
  :root {
    --sky: #c3f4fc;
    --mint: #dff6ee;
    --spring: #eef5c6;
    --cover-top: #6fdff9;
    --cover-mid: #f4fdfb;
    --cover-low: #cfe774;
    --ink: #3a48c8;
    --ink-soft: #4a63d2;
    --ornament: #5d9fe6;
    --frame-outer: #7fc0f7;
    --frame-line: #1d2340;
    --gold: #d9a640;
    --white: #ffffff;
  }
  * { margin: 0; padding: 0; box-sizing: border-box; }
  html, body { width: 848px; height: 1200px; overflow: hidden; background: var(--white); }
  .sheet { position: relative; width: 848px; height: 1200px; overflow: hidden; }

  .spread { position: absolute; left: 0; width: 848px; height: 600px;
    background: linear-gradient(180deg, var(--sky) 0%, var(--mint) 45%, var(--spring) 100%); }
  .spread--outside { top: 0; border-bottom: 1px solid #cfe3a0; }
  .spread--inside { top: 600px; }

  /* Cover */
  .cover { position: absolute; left: 426px; top: 0; width: 422px; height: 599px; overflow: hidden;
    background:
      radial-gradient(ellipse 70% 40% at 45% 55%, var(--cover-mid) 0%, rgba(244,253,251,0) 100%),
      linear-gradient(180deg, var(--cover-top) 0%, #b9eef6 30%, #e9f9f2 55%, #e4f3b8 78%, var(--cover-low) 100%); }
  .cover__flower { position: absolute; right: -20px; top: -10px; width: 200px; height: 180px; border-radius: 50%;
    background: radial-gradient(circle, rgba(255,255,255,0.55) 0%, rgba(255,255,255,0.15) 60%, rgba(255,255,255,0) 75%); }
  .cover__band { position: absolute; left: 0; top: 181px; width: 100%; height: 78px;
    background: linear-gradient(180deg, rgba(120,200,240,0.15), rgba(110,190,235,0.55) 50%, rgba(255,255,255,0.1)); }
  .cover__title { position: absolute; left: 0; width: 100%; top: 192px; text-align: center;
    font-family: "Great Vibes", cursive; font-size: 46px; color: var(--white);
    text-shadow: 0 0 2px rgba(60,120,200,0.6); }
  .cover__waves { position: absolute; left: 0; top: 320px; width: 422px; height: 240px; }
  .cover__rings { position: absolute; left: 341px; top: 542px; width: 66px; height: 45px; border-radius: 40%;
    background: radial-gradient(ellipse, #f6d58a 0%, var(--gold) 60%, rgba(217,166,64,0) 75%); }

  .ornament { position: absolute; border-radius: 40%;
    background: radial-gradient(ellipse at center, rgba(93,159,230,0.75) 0%, rgba(93,159,230,0.35) 55%, rgba(93,159,230,0) 75%); }
  .ornament--cover-top { left: 92px; top: 106px; width: 258px; height: 84px; }
  .ornament--cover-bottom { left: 92px; top: 256px; width: 258px; height: 84px; }
  .ornament--inside-top { left: 516px; top: 24px; width: 258px; height: 84px; }
  .ornament--inside-bottom { left: 516px; top: 492px; width: 258px; height: 84px; }

  /* Invitation card */
  .card { position: absolute; left: 439px; top: 110px; width: 396px; height: 380px;
    background: linear-gradient(180deg, #a9dcfb, var(--frame-outer)); padding: 8px 9px 10px 11px; }
  .card__inner { width: 100%; height: 100%; border: 1.5px solid var(--frame-line);
    background: linear-gradient(180deg, #dcf3ea 0%, #e6f4cf 100%);
    text-align: center; color: var(--ink-soft); font-family: "Questrial", sans-serif;
    font-size: 12.5px; line-height: 14.6px; padding-top: 10px; }
  .card__hosts { font-weight: 700; font-size: 13.5px; color: var(--ink); }
  .card__couple { font-family: "Pinyon Script", cursive; font-size: 25px; line-height: 43px; color: var(--ink); margin-top: 14px; }
  .card__details { margin-top: 20px; }
  .card__details p + p { margin-top: 14.6px; }
</style>
</head>
<body>
<main class="sheet">
  <section class="spread spread--outside">
    <div class="cover">
      <div class="cover__flower" role="img" aria-label="Faint daisy flower decoration"></div>
      <div class="ornament ornament--cover-top" role="img" aria-label="Blue filigree heart ornament"></div>
      <div class="cover__band"></div>
      <h1 class="cover__title">Wedding Invitation</h1>
      <div class="ornament ornament--cover-bottom" role="img" aria-label="Blue filigree heart ornament"></div>
      <svg class="cover__waves" viewBox="0 0 422 240" fill="none" stroke="rgba(255,255,255,0.7)" stroke-width="0.8">
        <path d="M0 110 C90 220 200 190 300 110 S400 20 422 10"/>
        <path d="M0 118 C90 228 205 198 305 118 S400 30 422 20"/>
        <path d="M0 126 C95 236 210 206 310 126 S402 40 422 30"/>
        <path d="M0 134 C95 244 215 214 315 134 S404 50 422 40"/>
        <path d="M0 142 C100 250 220 222 320 142 S406 60 422 50"/>
        <path d="M0 150 C100 256 225 230 325 150 S408 70 422 60"/>
      </svg>
      <div class="cover__rings" role="img" aria-label="Pair of gold wedding rings"></div>
    </div>
  </section>

  <section class="spread spread--inside">
    <div class="ornament ornament--inside-top" role="img" aria-label="Blue filigree heart ornament"></div>
    <article class="card">
      <div class="card__inner">
        <p class="card__hosts">Mr. and Mrs. Dwight Velmoran</p>
        <p>Request the honour of your presence</p>
        <p>At the marriage of their daughter</p>
        <div class="card__couple">
          <p>Maris Velmoran</p>
          <p>to</p>
          <p>Lionel Brask</p>
        </div>
        <div class="card__details">
          <p>Saturday, the eighteenth of April Two thousand and twelve<br>At three o'clock in the afternoon</p>
          <p>Saint Odric's Church<br>58 Wendle Street,South Hampton, New York</p>
          <p>Followed by a dinner at<br>Restaurant Ovilo, Marsh Lane 347<br>R.S.V.P. by the ninth of April</p>
        </div>
      </div>
    </article>
    <div class="ornament ornament--inside-bottom" role="img" aria-label="Blue filigree heart ornament"></div>
  </section>
</main>
</body>
</html>
```